Logo and Card design for KRV Home Solutions LLC

I need an edgier logo and business card designs. Current logo attached. I like the colors below. I would like the logo to incorporate a home in the design.
Title = Principal-Acquisitions
Email:KRVHOMESOLUTIONS@fernmail.example
555-214-0937
facebook
IG
2 sided business card with the front being contact info a slogan about selling a home fast. The back incorporating What we do. Buy houses, land, or commercial property as is. We find solutions to make the process of selling simple and fair.

Target Market(s)

Motivated house sellers.

Industry/Entity Type

Business

Contact Information for Business Card

Who we are: We are a Faith based Real Estate Investment Company. We pay cash for homes in any condition and can close quick. Whatever the reason you need to sell fast, we can help. We believe in creating win-win solutions to help you in your time of need. We care! We can help!

Logo Text

KRV Home Solutions LLC

Font styles to use
Sans Serif

Colors
33a6d7
0355a3
85abd2
cee9f5
9d9d9d
b2b2b2
ffffff

Requirements
Must have
• Old logo attached. I want something edgier.
• Company name, phone number, description on the back of what we can do. Pay all cash. Buy in as is condition. No fees,Commisions or closing costs.Close quick. No hassles with solutions to meet your unique situation.
• Call today for an offer within 24 hours.

```html
<!DOCTYPE html>
<html lang="en">
<head>
<meta charset="utf-8">
<title>KRV Home Solutions LLC – Business Card</title>
<link rel="stylesheet" href="https://fonts.googleapis.com/css2?family=Roboto:wght@400;500;700&family=Roboto+Condensed:wght@400;500;700&display=swap">
<style>
  :root {
    --navy: #1e3473;
    --band: #5f5f5f;
    --ink: #444444;
    --ink-soft: #4d4d4d;
    --paper: #f1f1f1;
    --paper-front: #f4f6f7;
    --white: #ffffff;
    --stage: #2a2a2a;
    --rule: #6b6b6b;
  }
  * { margin: 0; padding: 0; box-sizing: border-box; }
  html, body { width: 1200px; height: 960px; overflow: hidden; }
  body { background: var(--stage); position: relative; font-family: "Roboto", Arial, sans-serif; }

  .card { position: absolute; width: 600px; height: 343px; overflow: hidden; }
  .card--front { left: 314px; top: 113px; background: var(--paper-front); }
  .card--back { left: 311px; top: 472px; background: var(--paper); }

  .front__photo {
    position: absolute; left: 0; top: 0; width: 600px; height: 232px;
    background: linear-gradient(180deg, #eef1f3 0%, #e6e9ea 45%, #dfe3dc 70%, #d8dfd0 100%);
  }
  .company-name {
    font-family: "Roboto", Arial, sans-serif; font-weight: 500;
    line-height: 1; color: var(--ink); white-space: nowrap;
  }
  .front__company { position: absolute; left: 38px; top: 122px; font-size: 21px; }

  .benefits {
    position: absolute; right: 38px; top: 70px; list-style: none;
    font-family: "Roboto Condensed", Arial, sans-serif; font-size: 15px;
    line-height: 18px; color: var(--ink); text-align: right;
  }
  .benefits li { position: relative; padding-right: 12px; }
  .benefits li.dot::after {
    content: ""; position: absolute; right: 0; top: 7px;
    width: 5px; height: 5px; border-radius: 50%; background: var(--navy);
  }

  .front__band {
    position: absolute; left: 0; top: 232px; width: 600px; height: 111px;
    background: var(--band); color: var(--white);
  }
  .contact { position: absolute; left: 38px; top: 26px; list-style: none; font-size: 14.5px; line-height: 19px; }
  .contact li { display: flex; align-items: center; gap: 8px; }
  .contact svg { width: 14px; height: 14px; fill: var(--white); flex: none; }
  .person { position: absolute; right: 39px; top: 31px; text-align: right; }
  .person__name { font-family: "Roboto Condensed", Arial, sans-serif; font-weight: 500; font-size: 24px; line-height: 1.1; }
  .person__title { font-weight: 500; font-size: 15px; line-height: 1.35; }

  .back__company { position: absolute; left: 0; width: 600px; top: 92px; text-align: center; font-size: 24px; }
  .back__rule { position: absolute; left: 102px; top: 137px; width: 390px; height: 2px; background: var(--rule); }
  .back__copy { position: absolute; left: 0; width: 600px; top: 156px; text-align: center; }
  .back__heading { font-weight: 700; font-size: 15px; line-height: 20px; color: var(--navy); margin-bottom: 2px; }
  .back__text { font-size: 15.2px; line-height: 18px; color: var(--ink-soft); }
  .back__text + .back__heading { margin-top: 8px; }
</style>
</head>
<body>

<section class="card card--front">
  <div class="front__photo" role="img" aria-label="Faded photo of a two-storey suburban house with a front porch, lawn and trees"></div>
  <div class="company-name front__company">KRV Home Solutions LLC</div>
  <ul class="benefits">
    <li class="dot">Pay all cash. Buy in as is condition</li>
    <li class="dot">No fees,Commisions or closing costs</li>
    <li class="dot">Close quick. No hassles with</li>
    <li>solutions to meet your unique situation</li>
    <li class="dot">Call today for an offer within 24 hours</li>
  </ul>

  <div class="front__band">
    <ul class="contact">
      <li><svg viewBox="0 0 24 24"><path d="M6.6 10.8a15.1 15.1 0 0 0 6.6 6.6l2.2-2.2a1 1 0 0 1 1-.25 11.4 11.4 0 0 0 3.6.57 1 1 0 0 1 1 1V20a1 1 0 0 1-1 1A17 17 0 0 1 3 4a1 1 0 0 1 1-1h3.5a1 1 0 0 1 1 1c0 1.25.2 2.45.57 3.57a1 1 0 0 1-.25 1z"/></svg>555-214-0937</li>
      <li><svg viewBox="0 0 24 24"><path d="M2 5h20v14H2z"/><path d="M2.5 5.5l9.5 6.6 9.5-6.6" fill="none" stroke="#5f5f5f" stroke-width="1.8"/></svg>KRVHOMESOLUTIONS@fernmail.example</li>
      <li><svg viewBox="0 0 24 24"><circle cx="12" cy="12" r="10"/><path d="M2 12h20M12 2c3 3 3 17 0 20M12 2c-3 3-3 17 0 20" fill="none" stroke="#5f5f5f" stroke-width="1.6"/></svg>KRVHOMESOLUTIONS.example</li>
    </ul>
    <div class="person">
      <div class="person__name">JORDAN REYES</div>
      <div class="person__title">Principal-Acquisitions</div>
    </div>
  </div>
</section>

<section class="card card--back">
  <div class="company-name back__company">KRV Home Solutions LLC</div>
  <div class="back__rule"></div>
  <div class="back__copy">
    <h2 class="back__heading">WHO WE ARE</h2>
    <p class="back__text">We are a Faith based Real Estate Investment Company. We pay cash for<br>homes in any condition and can close quick. Whatever the reason you need<br>to sell fast, we can help. We believe in creating win-win solutions to help</p>
    <h2 class="back__heading">WHAT WE DO</h2>
    <p class="back__text">Buy houses, land, or commercial property as is.<br>We find solutions to make the process of selling simple and fair.</p>
  </div>
</section>

</body>
</html>
```